Business Cards for IT Consulting Company (Managed Service Provider)

I am looking to have some business cards printed and would like some designs. We are an IT Consulting company based in Vancouver BC. I would like a nice clean and modern look to the cards. I have uploaded all the versions of my logo so parts can be used as needed. Here is a snippit from our website homepage:

Quillbrook Networks Ltd. is an IT Solutions Partner located in Vancouver BC, Canada. We offer IT solutions and support to customers in the greater Vancouver Area. With expertise in Microsoft platforms, as well as Linux and Mac OSX and over 12 years experience in the IT industry, Quillbrook Networks is dedicated to offering our clients top quality service and products. We take pride in the solutions we offer our customers. The greatest compliment a client can give us is to recommend our services.

Quillbrook Networks Ltd. offers a wide range of IT services from onsite service to remote support and managed service solutions. This allows clients to choose the support path that best suits their company’s needs. Supporting many different sized companies from small to enterprise level over the past 12 years Quillbrook Networks has the experience and expertise needed to ensure things run smoothly. Allowing our clients to focus on doing business.

Revolutionizing the way IT services are delivered.

Quillbrook Networks is dedicated to providing our clients with IT solutions that work and grow with them for years to come. This philosophy helps save money in the long run instead of replacing equipment constantly. Far too often IT solutions are not well thought out and while possibly solving the problem at hand, require replacement due to growth or quality within a very short time frame. Quillbrook Networks takes pride in providing solutions that will last and be able to accommodate growth without the need for replacement.

Industry/Entity Type

Information Technology

Contact Information for Business Card

Quillbrook Networks Ltd.
(Employee Name)
Eml: (Employees Email Address)
Web: quillbrook.me
Ph: 604-555-0148

Font styles to use
Serif
Sans Serif

Requirements
Must have
• The Company logo and company colors.
Nice to have
• - Our tag line: "Reliable IT, Built to Last" or "Revolutionizing the way IT services are delivered."
• - Also I really like the idea of nature and technology together blending which is sort of where my logo came from so integrating that somehow onto the business cards would be great.

```html
<!DOCTYPE html>
<html lang="en">
<head>
<meta charset="utf-8">
<title>Quillbrook Networks Ltd. — Business Cards</title>
<link rel="stylesheet" href="https://fonts.googleapis.com/css2?family=Montserrat:wght@500;600&family=Roboto:ital,wght@0,400;0,500;1,400&display=swap">
<style>
  :root {
    --backdrop: #a3a1a1;
    --card: #1f1f20;
    --brand-blue: #2b8fd6;
    --silver: #9a9a9a;
    --text-light: #e8e8e8;
    --text-muted: #d4d4d4;
  }
  * { box-sizing: border-box; margin: 0; padding: 0; }
  html, body {
    width: 1200px; height: 1200px; overflow: hidden;
    background: var(--backdrop);
  }
  .canvas { position: relative; width: 1200px; height: 1200px; }

  .card {
    position: absolute; width: 713px; height: 418px;
    background: var(--card); overflow: hidden;
  }
  .card--front { left: 238px; top: 118px; }
  .card--back  { left: 231px; top: 644px; }

  .brand {
    position: absolute; display: flex; align-items: center; gap: 22px;
  }
  .brand__square {
    border: 4px solid var(--brand-blue); flex: none;
  }
  .brand__name {
    font-family: "Montserrat", sans-serif; font-weight: 600;
    color: var(--brand-blue); line-height: 1;
  }
  .brand__name span { display: block; }
  .card--front .brand { left: 110px; top: 130px; }
  .card--front .brand__square { width: 92px; height: 92px; }
  .card--front .brand__word { font-size: 62px; letter-spacing: -0.5px; }
  .card--front .brand__sub { font-size: 24px; letter-spacing: 1px; margin-top: 8px; }

  .tagline {
    position: absolute; left: 0; right: 0; top: 376px;
    display: flex; align-items: center; justify-content: center; gap: 16px;
    font-family: "Montserrat", sans-serif; font-weight: 500; font-size: 18px;
    color: var(--text-light);
  }
  .tagline__rule { width: 110px; height: 2px; background: var(--brand-blue); }

  /* Back: plain edge bands */
  .edge-band {
    position: absolute; top: 0; bottom: 0; left: 0; width: 12px;
    background: var(--brand-blue);
  }
  .edge-rule {
    position: absolute; top: 34px; bottom: 34px; left: 30px; width: 2px;
    background: var(--silver);
  }

  .person {
    position: absolute; right: 375px; top: 128px; text-align: right;
    font-family: "Roboto", sans-serif;
  }
  .person__name {
    font-family: "Montserrat", sans-serif; font-weight: 600;
    font-size: 25px; color: var(--brand-blue);
  }
  .person__title { font-style: italic; font-size: 16px; color: var(--text-light); margin-top: 6px; }
  .contacts {
    position: absolute; right: 375px; top: 208px; list-style: none;
    font-family: "Roboto", sans-serif; font-size: 17.5px; color: var(--text-muted);
  }
  .contacts li {
    display: flex; align-items: center; justify-content: flex-end; gap: 13px;
    height: 27.5px;
  }
  .contacts svg { width: 17px; height: 17px; flex: none; }
  .card--back .brand { left: 388px; top: 120px; flex-direction: column; align-items: center; gap: 22px; }
  .card--back .brand__square { width: 80px; height: 80px; }
  .card--back .brand__name { text-align: center; }
  .card--back .brand__word { font-size: 42px; }
  .card--back .brand__sub { font-size: 17px; letter-spacing: 1px; margin-top: 6px; }
</style>
</head>
<body>
<main class="canvas">

  <section class="card card--front" aria-label="Card front">
    <div class="brand">
      <div class="brand__square"></div>
      <div class="brand__name">
        <span class="brand__word">Quillbrook</span>
        <span class="brand__sub">NETWORKS LTD.</span>
      </div>
    </div>
    <p class="tagline">
      <span class="tagline__rule"></span>
      Reliable IT, Built to Last
      <span class="tagline__rule"></span>
    </p>
  </section>

  <section class="card card--back" aria-label="Card back">
    <div class="edge-band"></div>
    <div class="edge-rule"></div>

    <div class="person">
      <p class="person__name">Daniel Harper</p>
      <p class="person__title">Managing Director</p>
    </div>

    <ul class="contacts">
      <li>604-555-0148
        <svg viewBox="0 0 24 24" fill="var(--brand-blue)" aria-hidden="true"><path d="M6.6 10.8a15.1 15.1 0 0 0 6.6 6.6l2.2-2.2a1 1 0 0 1 1-.25 11.4 11.4 0 0 0 3.6.57 1 1 0 0 1 1 1V20a1 1 0 0 1-1 1A17 17 0 0 1 3 4a1 1 0 0 1 1-1h3.5a1 1 0 0 1 1 1c0 1.25.2 2.45.57 3.6a1 1 0 0 1-.25 1z"/></svg>
      </li>
      <li>www.quillbrook.me
        <svg viewBox="0 0 24 24" fill="none" stroke="var(--brand-blue)" stroke-width="2" aria-hidden="true"><circle cx="12" cy="12" r="9"/><path d="M3 12h18M12 3c3 3 3 15 0 18M12 3c-3 3-3 15 0 18"/></svg>
      </li>
      <li>support@quillbrook.me
        <svg viewBox="0 0 24 24" fill="var(--brand-blue)" aria-hidden="true"><path d="M2 5h20v14H2z"/><path d="M2 5l10 8 10-8" fill="none" stroke="var(--card)" stroke-width="2"/></svg>
      </li>
    </ul>

    <div class="brand">
      <div class="brand__square"></div>
      <div class="brand__name">
        <span class="brand__word">Quillbrook</span>
        <span class="brand__sub">NETWORKS LTD.</span>
      </div>
    </div>
  </section>

</main>
</body>
</html>
```